Telecommunications/Power civil contractor needs business card design

Were a new telecommunications/power underground civil contractor that is looking for a new business card design. Our company colours are silver or grey and orange. Feel free to use the white background logo or the black background logo.

Target Market(s)

Local contractors, utility companies, private sector mining/energy companies, developers.

Industry/Entity Type

Telecommunications

Contact Information for Business Card

Each card will need the following info:
Persons name:
Title:
E-mail:
Phone number:
Shop Address:
Mailing Address:

Requirements
Must have
• Each card will need the following info:
• Persons name:
• Title:
• E-mail:
• Phone number:
• Shop Address:
• Mailing Address:

```html
<!DOCTYPE html>
<html lang="en">
<head>
<meta charset="utf-8">
<title>Trenchline Contracting Inc – Business Card</title>
<link rel="stylesheet" href="https://fonts.googleapis.com/css2?family=Montserrat:wght@400;500;700;800&display=swap">
<style>
  :root {
    --page: #e9e6e1;
    --card: #0d0d0d;
    --card-edge: #1c1c1c;
    --orange: #ef6a2b;
    --silver: #a9a9a9;
    --silver-light: #d6d6d6;
    --white: #f4f4f4;
  }
  * { box-sizing: border-box; margin: 0; padding: 0; }
  html, body { width: 1200px; height: 1022px; overflow: hidden; }
  body {
    background: var(--page);
    font-family: "Montserrat", Arial, sans-serif;
    display: flex;
    flex-direction: column;
    align-items: center;
    justify-content: center;
    gap: 60px;
  }
  .card {
    position: relative;
    width: 700px;
    height: 400px;
    border-radius: 18px;
    background: linear-gradient(135deg, var(--card-edge) 0%, var(--card) 55%);
    box-shadow: 0 10px 28px rgba(0,0,0,.28);
    overflow: hidden;
  }
  /* Front */
  .front .details {
    position: absolute;
    left: 48px;
    top: 42px;
    color: var(--white);
  }
  .company-name {
    font-weight: 800;
    font-size: 27px;
    line-height: 1.1;
    letter-spacing: .5px;
    color: var(--orange);
    width: 300px;
  }
  .person-name {
    margin-top: 22px;
    font-weight: 500;
    font-size: 25px;
    letter-spacing: 1px;
    color: var(--orange);
    text-transform: uppercase;
  }
  .person-title {
    font-size: 15px;
    color: var(--white);
    margin-top: 2px;
  }
  .address {
    margin-top: 20px;
    font-size: 15px;
    line-height: 1.45;
    letter-spacing: .3px;
  }
  .address + .address { margin-top: 10px; }
  .contact-list {
    list-style: none;
    margin-top: 16px;
    font-size: 15px;
    line-height: 1.5;
  }
  .contact-list li { display: flex; align-items: center; gap: 10px; }
  .contact-list svg { width: 14px; height: 14px; flex: none; }
  .front .ring {
    position: absolute;
    right: -70px;
    top: 40px;
    width: 320px;
    height: 320px;
  }
  /* Back */
  .back {
    display: flex;
    align-items: center;
    justify-content: center;
    gap: 28px;
  }
  .back .ring { width: 120px; height: 120px; flex: none; }
  .back .company-name {
    width: auto;
    font-size: 32px;
    color: var(--silver-light);
    line-height: 1.2;
  }
</style>
</head>
<body>

<section class="card front" aria-label="Business card front">
  <div class="details">
    <h1 class="company-name">TRENCHLINE<br>CONTRACTING INC</h1>
    <p class="person-name">Marla Kessler</p>
    <p class="person-title">Director</p>
    <p class="address">48 Quarry Lane<br>Ashford Falls, NY 12000</p>
    <p class="address">PO BOX 3150<br>BROOKHAVEN, CA 90000</p>
    <ul class="contact-list">
      <li>
        <svg viewBox="0 0 16 16" fill="none" stroke="var(--orange)" stroke-width="1.6"><rect x="4" y="1" width="8" height="14" rx="1.5"/><line x1="7" y1="12.5" x2="9" y2="12.5"/></svg>
        +330 5550-0142
      </li>
      <li>
        <svg viewBox="0 0 16 16" fill="var(--orange)"><path d="M3.2 1.5l2.4-.4 1.3 3.3-1.6 1.1a8.6 8.6 0 0 0 4.9 4.9l1.1-1.6 3.3 1.3-.4 2.4c-.2.8-.9 1.3-1.7 1.2C6.9 13.3 2.7 9.1 2.3 3.3c-.1-.9.2-1.6.9-1.8z"/></svg>
        +330 5550-0187
      </li>
      <li>
        <svg viewBox="0 0 16 16" fill="none" stroke="var(--orange)" stroke-width="1.6"><rect x="1.5" y="3" width="13" height="10" rx="1"/><polyline points="1.5,3.5 8,9 14.5,3.5"/></svg>
        info@trenchlinecontracting.com
      </li>
      <li>
        <svg viewBox="0 0 16 16" fill="none" stroke="var(--orange)" stroke-width="1.4"><circle cx="8" cy="8" r="6.5"/><ellipse cx="8" cy="8" rx="3" ry="6.5"/><line x1="1.5" y1="8" x2="14.5" y2="8"/></svg>
        www.trenchlinecontracting.com
      </li>
    </ul>
  </div>
  <svg class="ring" viewBox="0 0 320 320" aria-hidden="true">
    <circle cx="160" cy="160" r="148" fill="none" stroke="var(--silver)" stroke-width="16"/>
  </svg>
</section>

<section class="card back" aria-label="Business card back">
  <svg class="ring" viewBox="0 0 120 120" aria-hidden="true">
    <circle cx="60" cy="60" r="52" fill="none" stroke="var(--orange)" stroke-width="10"/>
  </svg>
  <h2 class="company-name">TRENCHLINE<br>CONTRACTING INC</h2>
</section>

</body>
</html>
```